Copperleaf Balustrade Website Redesign

I want a fresh new design for my website. Original website
www.copperleafbalustrade-example.com. Will need to add additional photos for winning designer. Please use the basic layout for new design. Looking to get a more modern, functional site to attract new customer and ne bale to highlight past projects. Need it to be easy to navigate and get in touch with me for inquiries.

Target Market(s)

Builders and home owners in WA state

Industry/Entity Type

Building, Construction, Deck building

Coding

Coded - Design and coding required

Number of Pages Required

5+ page

Font styles to use
Sans Serif

Colors
0054AA
0677BA
7BADD7
CADEEF
E8F1F8
0094D4
00A9DD
6FCCEA
C7EBF8
E9F6FB
00AB8E
00BBA5
67D7C9
C6EFE9
E9F9F6
59FF00
82FF00
B8FF75
E3FFCB
F4FFEA

Requirements
Must have
• Will need to add more photos of completed projects
Nice to have
• Fresh take on old website, something modern
Should not have
• Nothing comes to mind

```html
<!DOCTYPE html>
<html lang="en">
<head>
<meta charset="UTF-8">
<title>Contact – Copperleaf Balustrade</title>
<link rel="stylesheet" href="https://fonts.googleapis.com/css2?family=Inter:wght@500;600;700;800&family=Jost:wght@400;500;600&display=swap">
<style>
  :root {
    --brand: #066a3c;
    --brand-light: #2e9d5a;
    --ink: #111111;
    --muted: #8a8a8a;
    --field-border: #9fcdbd;
    --card-bg: #e8f6f3;
    --card-border: #9fd4c0;
    --footer-bg: #000000;
    --white: #ffffff;
  }
  * { box-sizing: border-box; margin: 0; padding: 0; }
  html, body { width: 974px; height: 1200px; overflow: hidden; background: var(--white); }
  body { position: relative; font-family: 'Jost', sans-serif; color: var(--ink); }

  .site-header { position: absolute; left: 0; top: 0; width: 974px; height: 75px; background: var(--white); }
  .brand { position: absolute; left: 47px; top: 20px; display: flex; align-items: center; gap: 8px; }
  .brand-mark { width: 26px; height: 26px; background: var(--brand); }
  .brand-name { font-family: 'Jost', sans-serif; font-weight: 500; font-size: 17px; line-height: 18px; color: var(--brand); text-transform: uppercase; letter-spacing: 0.3px; }
  .main-nav { position: absolute; top: 25px; right: 47px; display: flex; align-items: center; gap: 0; }
  .main-nav a { font-family: 'Inter', sans-serif; font-weight: 600; font-size: 11px; color: var(--ink); text-decoration: none; margin-left: 38px; }
  .main-nav .nav-cta { background: var(--brand); color: var(--white); padding: 8px 8px; height: 29px; display: inline-flex; align-items: center; }

  .hero { position: absolute; left: 0; top: 75px; width: 974px; height: 278px; }
  .hero-photo { position: absolute; inset: 0;
    background:
      linear-gradient(90deg, rgba(0,0,0,0.55) 0%, rgba(0,0,0,0.15) 40%, rgba(0,0,0,0) 60%),
      linear-gradient(180deg, #7a4a34 0%, #5c3a28 35%, #2a2520 60%, #b07c4c 80%, #1a1410 100%); }
  .hero-title { position: absolute; left: 47px; top: 114px; font-family: 'Inter', sans-serif; font-weight: 800; font-size: 32px; color: var(--white); letter-spacing: 0.5px; }

  .quote-intro { position: absolute; left: 0; top: 383px; width: 974px; text-align: center; }
  .quote-intro h2 { font-family: 'Inter', sans-serif; font-weight: 800; font-size: 21px; color: var(--brand); letter-spacing: 0.3px; }
  .quote-intro p { font-family: 'Inter', sans-serif; font-size: 10.5px; margin-top: 8px; }

  .field-label { position: absolute; font-weight: 600; font-size: 11px; }
  .field { position: absolute; height: 29px; border: 1px solid var(--field-border); border-radius: 15px; padding-left: 12px; font-size: 9.5px; color: var(--muted); display: flex; align-items: center; }
  .field-message { height: 126px; border-radius: 9px; align-items: flex-start; padding: 12px 14px; font-size: 11px; }
  .send-button { position: absolute; left: 95px; top: 733px; width: 786px; height: 34px; border-radius: 17px; background: var(--brand); color: var(--white); font-family: 'Inter', sans-serif; font-weight: 600; font-size: 11px; display: flex; align-items: center; justify-content: center; }

  .info-card { position: absolute; top: 806px; width: 253px; height: 141px; background: var(--card-bg); border: 1px solid var(--card-border); border-radius: 7px; text-align: center; }
  .info-icon { position: absolute; left: 97px; top: 15px; width: 58px; height: 58px; border-radius: 50%; background: var(--brand); display: flex; align-items: center; justify-content: center; }
  .info-text { position: absolute; left: 0; width: 100%; font-weight: 600; font-size: 16px; line-height: 23px; }

  .site-footer { position: absolute; left: 0; top: 986px; width: 974px; height: 214px; background: var(--footer-bg); color: var(--white); }
  .footer-brand { position: absolute; left: 47px; top: 40px; display: flex; align-items: center; gap: 10px; }
  .footer-brand .brand-mark { width: 30px; height: 30px; background: var(--brand-light); }
  .footer-brand .brand-name { color: var(--brand-light); font-weight: 400; font-size: 20px; line-height: 22px; }
  .footer-about { position: absolute; left: 47px; top: 100px; width: 290px; font-size: 10.5px; line-height: 16.5px; }
  .footer-col { position: absolute; top: 36px; }
  .footer-col h3 { font-family: 'Inter', sans-serif; font-weight: 600; font-size: 11px; color: var(--brand-light); margin-bottom: 12px; }
  .footer-col li { list-style: none; font-size: 11px; height: 24.7px; display: flex; align-items: center; }
  .footer-col li::before { content: ""; width: 4px; height: 4px; background: var(--brand-light); transform: rotate(45deg); margin: 0 12px 0 3px; }
  .social-list { display: flex; gap: 8px; }
  .social-dot { width: 25px; height: 25px; border-radius: 50%; background: var(--brand-light); }
  .footer-rule { position: absolute; left: 0; top: 176px; width: 974px; height: 1px; background: #3a3a3a; }
  .copyright { position: absolute; left: 0; top: 187px; width: 974px; text-align: center; font-size: 11px; }
</style>
</head>
<body>
  <header class="site-header">
    <div class="brand">
      <span class="brand-mark"></span>
      <span class="brand-name">Copperleaf<br>Balustrade</span>
    </div>
    <nav class="main-nav">
      <a href="#">HOME</a>
      <a href="#">ABOUT</a>
      <a href="#">PRODUCT</a>
      <a href="#">WHY CHOOSE US</a>
      <a href="#" class="nav-cta">CONTACT</a>
    </nav>
  </header>

  <section class="hero">
    <div class="hero-photo" role="img" aria-label="Customer service representative with a headset working at a laptop in a bright office with plants"></div>
    <h1 class="hero-title">CONTACT</h1>
  </section>

  <section class="quote-intro">
    <h2>REQUEST A QUOTE</h2>
    <p>Let's build your dream outdoor space together</p>
  </section>

  <form class="quote-form">
    <label class="field-label" style="left:96px;top:449px">First Name</label>
    <div class="field" style="left:96px;top:470px;width:385px">First Name</div>
    <label class="field-label" style="left:497px;top:449px">Last Name</label>
    <div class="field" style="left:497px;top:470px;width:385px">Last Name</div>

    <label class="field-label" style="left:96px;top:510px">E - Mail</label>
    <div class="field" style="left:96px;top:531px;width:385px">E - Mail</div>
    <label class="field-label" style="left:497px;top:510px">Subject</label>
    <div class="field" style="left:497px;top:531px;width:385px">Subject</div>

    <label class="field-label" style="left:96px;top:573px">Message</label>
    <div class="field field-message" style="left:96px;top:594px;width:786px">Message...</div>

    <div class="send-button">SEND MESSAGE</div>
  </form>

  <div class="info-card" style="left:96px">
    <div class="info-icon">
      <svg width="30" height="30" viewBox="0 0 24 24"><path fill="#fff" d="M6.6 10.8a15.1 15.1 0 0 0 6.6 6.6l2.2-2.2c.3-.3.7-.4 1-.2 1.1.4 2.3.6 3.6.6.6 0 1 .4 1 1V20c0 .6-.4 1-1 1A17 17 0 0 1 3 4c0-.6.4-1 1-1h3.5c.6 0 1 .4 1 1 0 1.3.2 2.5.6 3.6.1.3 0 .7-.2 1z"/></svg>
    </div>
    <p class="info-text" style="top:94px">(509) 555-0148</p>
  </div>

  <div class="info-card" style="left:363px">
    <div class="info-icon">
      <svg width="28" height="30" viewBox="0 0 24 26"><path fill="#fff" d="M12 1a8 8 0 0 0-8 8c0 5.5 8 15 8 15s8-9.5 8-15a8 8 0 0 0-8-8zm0 11a3 3 0 1 1 0-6 3 3 0 0 1 0 6z"/></svg>
    </div>
    <p class="info-text" style="top:84px">4817 Juniper Ridge Ave<br>Yakima, WA 98902</p>
  </div>

  <div class="info-card" style="left:629px">
    <div class="info-icon">
      <svg width="34" height="34" viewBox="0 0 24 24" fill="none" stroke="#fff" stroke-width="2"><circle cx="12" cy="12" r="9"/><ellipse cx="12" cy="12" rx="4" ry="9"/><line x1="3" y1="12" x2="21" y2="12"/><line x1="12" y1="3" x2="12" y2="21"/></svg>
    </div>
    <p class="info-text" style="top:94px;font-size:12px">www.copperleafbalustrade-example.com</p>
  </div>

  <footer class="site-footer">
    <div class="footer-brand">
      <span class="brand-mark"></span>
      <span class="brand-name">COPPERLEAF<br>BALUSTRADE</span>
    </div>
    <p class="footer-about">we specialize in crafting custom railing systems designed to withstand the region's unique climate while enhancing the beauty of your outdoor living spaces.</p>

    <div class="footer-col" style="left:410px">
      <h3>QUICK LINKS</h3>
      <ul><li>Home</li><li>Product</li><li>Why Choose us</li><li>Contact</li></ul>
    </div>
    <div class="footer-col" style="left:589px">
      <h3>OUR PRODUCT</h3>
      <ul><li>Aluminum Railings</li><li>Glass Railings</li><li>Cable Railings</li><li>Custom design</li></ul>
    </div>
    <div class="footer-col" style="left:800px">
      <h3>CONNECT WITH US</h3>
      <div class="social-list">
        <span class="social-dot"></span><span class="social-dot"></span><span class="social-dot"></span><span class="social-dot"></span>
      </div>
    </div>

    <div class="footer-rule"></div>
    <p class="copyright">© Copyright 2024&nbsp; All Rights Reserved</p>
  </footer>
</body>
</html>
```